i need a business card for a plumbing company in california

we are a drain cleaning , maintenance plumbing company who is starting new marketing campaign for a tatrench-less pipe installation department .

Target Market(s)

the professional who appreciates time and quality workmanship.

Industry/Entity Type

Plumbing

Colors
0655a3
ec1f27

Requirements
Must have
• the second logo needs to be included
Nice to have
• a focus on the services offered
Should not have
• any underlined words on the brief

```html
<!DOCTYPE html>
<html lang="en">
<head>
<meta charset="utf-8">
<title>Clearline Plumbing – Business Card</title>
<link rel="stylesheet" href="https://fonts.googleapis.com/css2?family=Roboto:wght@400;700;900&display=swap">
<style>
  :root {
    --brand-red: #e0282f;
    --brand-red-dark: #c81f26;
    --band-grey: #a4a198;
    --logo-grey: #8a8880;
    --paper: #f6f6f4;
    --ink-white: #ffffff;
    --backdrop: #e7e2da;
  }
  * { box-sizing: border-box; margin: 0; padding: 0; }
  html, body {
    width: 1200px; height: 780px; overflow: hidden;
    background: var(--backdrop);
    font-family: "Roboto", Arial, sans-serif;
  }
  .canvas {
    position: relative; width: 1200px; height: 780px;
    display: flex; align-items: center; justify-content: center; gap: 40px;
  }
  .card {
    position: relative; width: 560px; height: 320px; overflow: hidden;
    box-shadow: 0 6px 18px rgba(0,0,0,.18);
  }

  /* Front */
  .card-front { background: var(--paper); }
  .front-logo {
    position: absolute; left: 40px; top: 62px;
    display: flex; align-items: center; gap: 14px;
  }
  .logo-dot {
    width: 30px; height: 30px; border-radius: 50%;
    background: var(--brand-red);
  }
  .front-logo .logo-name {
    font-weight: 900; font-size: 38px; line-height: 1;
    color: var(--logo-grey); letter-spacing: -0.5px;
  }
  .grey-band {
    position: absolute; left: 0; right: 0; top: 160px; height: 22px;
    background: var(--band-grey);
  }
  .red-panel {
    position: absolute; left: 0; right: 0; top: 182px; bottom: 0;
    background: linear-gradient(180deg, var(--brand-red), var(--brand-red-dark));
    padding: 14px 40px; color: var(--ink-white);
  }
  .person {
    position: absolute; left: 40px; top: 161px;
    font-size: 14px; color: var(--ink-white); line-height: 20px;
  }
  .person .name { font-weight: 700; }
  .person .divider { margin: 0 8px; opacity: .8; }
  .contact-list { list-style: none; font-size: 13px; line-height: 21px; }
  .contact-list li { display: flex; align-items: center; gap: 8px; }
  .contact-list .icon { width: 14px; height: 14px; flex: none; }
  .contact-list .no-icon { padding-left: 22px; }

  /* Back */
  .card-back {
    background: radial-gradient(ellipse at 55% 40%, var(--brand-red), var(--brand-red-dark));
  }
  .side-strip {
    position: absolute; left: 0; top: 0; bottom: 0; width: 52px;
    background: var(--band-grey);
    border-right: 3px solid var(--paper);
    display: flex; align-items: center; justify-content: center;
  }
  .side-strip .web {
    transform: rotate(90deg); white-space: nowrap;
    font-size: 12px; letter-spacing: 2px; color: #6f6d66;
  }
  .back-logo {
    position: absolute; left: 52px; right: 0; top: 0; bottom: 0;
    display: flex; align-items: center; justify-content: center; gap: 16px;
  }
  .back-logo .logo-dot { background: var(--ink-white); width: 34px; height: 34px; }
  .back-logo .logo-name {
    font-weight: 900; font-size: 44px; color: var(--ink-white); letter-spacing: -0.5px;
  }
</style>
</head>
<body>
<main class="canvas">

  <section class="card card-front" aria-label="Business card front">
    <div class="front-logo">
      <span class="logo-name">Clearline Plumbing</span>
      <span class="logo-dot"></span>
    </div>
    <div class="grey-band"></div>
    <p class="person"><span class="name">Dana Whitlock</span><span class="divider">|</span><span class="title">President</span></p>
    <div class="red-panel">
      <ul class="contact-list">
        <li class="no-icon">PO Box 480 Harbor Road</li>
        <li class="no-icon">Sacramento, CA</li>
        <li>
          <svg class="icon" viewBox="0 0 14 14"><circle cx="7" cy="7" r="6.5" fill="none" stroke="#fff"/><path d="M4.5 4h1.6l.6 1.6-.9.7a4.5 4.5 0 0 0 2 2l.7-.9 1.6.6V9.6A.9.9 0 0 1 9.2 10.5 5.8 5.8 0 0 1 3.6 4.9.9.9 0 0 1 4.5 4z" fill="#fff"/></svg>
          555 014 2290
        </li>
        <li>
          <svg class="icon" viewBox="0 0 14 14"><circle cx="7" cy="7" r="6.5" fill="none" stroke="#fff"/><rect x="3.5" y="4.5" width="7" height="5" fill="none" stroke="#fff"/><path d="M3.5 4.5 7 7.3l3.5-2.8" fill="none" stroke="#fff"/></svg>
          hello@clearlineplumb.com
        </li>
        <li>
          <svg class="icon" viewBox="0 0 14 14"><circle cx="7" cy="7" r="6.5" fill="none" stroke="#fff"/><circle cx="7" cy="7" r="3.5" fill="none" stroke="#fff"/><path d="M3.5 7h7M7 3.5v7" stroke="#fff" stroke-width=".8"/></svg>
          www.clearlineplumb.com
        </li>
      </ul>
    </div>
  </section>

  <section class="card card-back" aria-label="Business card back">
    <div class="side-strip"><span class="web">www.clearlineplumb.com</span></div>
    <div class="back-logo">
      <span class="logo-name">Clearline Plumbing</span>
      <span class="logo-dot"></span>
    </div>
  </section>

</main>
</body>
</html>
```